Business Card Design

Electronic Security Installation Specialists

Check out our website at www.tallbrookllc.com to see what we do.

Industry/Entity Type

Business

Contact Information for Business Card

Tall Brook
Marjorie Hadley
281 Orchard Rise
Mapleton, WV 25871

Colors
3176b5
0455a3
ffffff

```html
<!DOCTYPE html>
<html lang="en">
<head>
<meta charset="utf-8">
<title>Tall Brook – Business Card</title>
<link rel="stylesheet" href="https://fonts.googleapis.com/css2?family=Exo+2:wght@400;600&display=swap">
<style>
  :root {
    --brand-deep: #0455a3;
    --brand-mid: #3176b5;
    --paper: #ffffff;
    --swoosh-dark: #5d5f63;
    --swoosh-light: #a9abae;
    --stage: #e7e9ec;
  }
  html, body {
    margin: 0;
    width: 1200px;
    height: 901px;
    overflow: hidden;
    background: var(--stage);
    font-family: "Exo 2", sans-serif;
  }
  .business-card {
    position: absolute;
    left: 100px;
    top: 165px;
    width: 1000px;
    height: 571px;
    border-radius: 44px;
    overflow: hidden;
    background: var(--paper);
    box-shadow: 0 18px 40px rgba(0,0,0,0.18);
  }
  .card-artwork {
    position: absolute;
    inset: 0;
    width: 100%;
    height: 100%;
  }
  .brand-mark {
    position: absolute;
    left: 88px;
    top: 26px;
    width: 170px;
    height: 170px;
    border-radius: 50%;
    background: var(--brand-deep);
    box-shadow: 0 0 0 6px #e3e5e8;
    display: flex;
    align-items: center;
    justify-content: center;
  }
  .brand-name {
    color: var(--paper);
    font-weight: 600;
    font-size: 30px;
    letter-spacing: 1px;
  }
  .holder {
    position: absolute;
    left: 48px;
    top: 322px;
    color: var(--paper);
  }
  .holder-name {
    margin: 0;
    font-size: 34px;
    font-weight: 600;
    letter-spacing: 1px;
    text-transform: uppercase;
  }
  .holder-title {
    margin: 2px 0 0;
    font-size: 16px;
    letter-spacing: 1.5px;
    text-transform: uppercase;
  }
  .contact {
    position: absolute;
    right: 48px;
    bottom: 40px;
    color: var(--paper);
    text-align: right;
    font-size: 19px;
    line-height: 1.2;
  }
  .contact-address {
    margin: 0 0 20px;
    font-size: 21px;
    font-style: normal;
  }
  .contact-list {
    list-style: none;
    margin: 0;
    padding: 0;
  }
  .contact-list li {
    display: flex;
    justify-content: flex-end;
    align-items: center;
    gap: 12px;
    margin-top: 10px;
  }
  .contact-icon {
    width: 18px;
    height: 18px;
    fill: none;
    stroke: var(--paper);
    stroke-width: 1.8;
  }
</style>
</head>
<body>
  <article class="business-card">
    <svg class="card-artwork" viewBox="0 0 1000 571" preserveAspectRatio="none" aria-hidden="true">
      <defs>
        <linearGradient id="band-fill" x1="0" y1="1" x2="1" y2="0">
          <stop offset="0" stop-color="#0455a3"/>
          <stop offset="0.55" stop-color="#3176b5"/>
          <stop offset="1" stop-color="#0455a3"/>
        </linearGradient>
      </defs>
      <path d="M0,205 C200,270 420,300 600,270 C760,245 880,200 1000,150" fill="none" stroke="var(--swoosh-dark)" stroke-width="11"/>
      <path d="M0,222 C200,290 420,318 600,290 C760,262 880,218 1000,168 L1000,571 L0,571 Z" fill="url(#band-fill)"/>
      <path d="M420,322 C620,338 800,290 1000,195" fill="none" stroke="var(--swoosh-dark)" stroke-width="9" opacity="0.9"/>
      <path d="M460,345 C650,355 820,300 1000,225" fill="none" stroke="var(--swoosh-light)" stroke-width="7" opacity="0.8"/>
    </svg>

    <div class="brand-mark">
      <span class="brand-name">Tall Brook</span>
    </div>

    <div class="holder">
      <h1 class="holder-name">Marjorie Hadley</h1>
      <p class="holder-title">Managing Director</p>
    </div>

    <div class="contact">
      <address class="contact-address">281 Orchard Rise<br>Mapleton, WV 25871</address>
      <ul class="contact-list">
        <li>304 555 0142
          <svg class="contact-icon" viewBox="0 0 20 20"><path d="M4 2 L8 2 L9 6 L7 8 C8 11 9 12 12 13 L14 11 L18 12 L18 16 C10 17 3 10 4 2 Z"/></svg>
        </li>
        <li>304 555 0176
          <svg class="contact-icon" viewBox="0 0 20 20"><rect x="6" y="2" width="8" height="16" rx="1.5"/><line x1="9" y1="15" x2="11" y2="15"/></svg>
        </li>
        <li>304 555 0190
          <svg class="contact-icon" viewBox="0 0 20 20"><rect x="3" y="8" width="14" height="9" rx="1"/><rect x="6" y="3" width="8" height="5"/></svg>
        </li>
        <li>hello@tallbrookllc.com
          <svg class="contact-icon" viewBox="0 0 20 20"><rect x="2" y="5" width="16" height="11"/><path d="M2 5 L10 11 L18 5"/></svg>
        </li>
        <li>www.tallbrookllc.com
          <svg class="contact-icon" viewBox="0 0 20 20"><circle cx="10" cy="10" r="8"/><ellipse cx="10" cy="10" rx="3.5" ry="8"/><line x1="2" y1="10" x2="18" y2="10"/></svg>
        </li>
      </ul>
    </div>
  </article>
</body>
</html>
```